A comprehensive online math curriculum teaching service needs a Landing Page design

We need a Landing Page design for a startup company based in Edmonton, Alberta, Canada, called Brevanta Numérica. Brevanta Numérica is a comprehensive online math curriculum service for independently schooled students in grades 6-12 worldwide. Instruction is delivered through a one-on-one, virtual, adaptive classroom that uses integrated, interactive digital whiteboards for both teachers and students, with a standard modular lesson workflow for mastering math. Brevanta Numérica is designed to help students from all socioeconomic backgrounds master mathematics.

The landing Page should use the same colour scheme as our recently designed PowerPoint template (attached for reference: Design 36712224). Our logo is in the PowerPoint template. I also attached a draft wireframe of our landing page to guide the design.

Target Market(s)

Independently schooled students in grades 6 through 12 worldwide

Industry/Entity Type

Education - Mathematics teaching

Requirements
Must have
• Consistent colours with PowerPoint design

```html
<!DOCTYPE html>
<html lang="en">
<head>
<meta charset="utf-8">
<title>Brevanta Numérica — Inspiring Math, Empowering Learning</title>
<link href="https://fonts.googleapis.com/css2?family=Montserrat:wght@500;600;700;800&family=Inter:wght@400;500;600&display=swap" rel="stylesheet">
<style>
:root{
  --green-dark:#1f4a33;
  --green:#2f6b4a;
  --green-light:#4a8a66;
  --blue:#3b82f6;
  --blue-soft:#dfe9fb;
  --ink:#1c1c1c;
  --body:#3a3a3a;
  --muted:#555;
  --white:#ffffff;
  --paper:#f4f3f3;
  --footer:#1f2330;
  --line:#c9d6ee;
}
*{box-sizing:border-box;margin:0;padding:0}
html,body{width:1200px;height:3515px;overflow:hidden}
body{font-family:'Inter',sans-serif;color:var(--body);background:var(--white);position:relative}
.section{position:absolute;left:0;width:1200px}
.chalkboard{background:radial-gradient(ellipse at 50% 40%,var(--green-light) 0%,var(--green) 45%,var(--green-dark) 100%)}
.heading{font-family:'Montserrat',sans-serif;font-weight:800;text-transform:uppercase;letter-spacing:.5px}
.btn{display:inline-block;font-family:'Montserrat',sans-serif;font-weight:700;font-size:11px;text-transform:uppercase;padding:11px 13px;text-decoration:none;letter-spacing:.2px;white-space:nowrap}
.btn-blue{background:var(--blue);color:var(--white)}
.btn-white{background:var(--white);color:var(--ink)}

/* hero */
.hero{top:0;height:672px}
.hero-bg{position:absolute;inset:0}
.brand{position:absolute;left:30px;top:26px;display:flex;align-items:center;gap:14px;color:var(--white)}
.brand-mark{width:26px;height:26px;border-radius:50%;background:var(--white)}
.brand-name{font-family:'Montserrat',sans-serif;font-weight:500;font-size:22px;line-height:1;white-space:nowrap}
.brand-tag{font-size:11px;margin-top:6px;opacity:.9;white-space:nowrap}
.nav{position:absolute;left:350px;top:40px;display:flex;gap:27px}
.nav a{font-family:'Montserrat',sans-serif;font-weight:700;font-size:13px;color:var(--white);text-decoration:none;padding-bottom:8px;white-space:nowrap}
.nav a.active{border-bottom:3px solid var(--white)}
.nav-cta{position:absolute;right:47px;top:32px;display:flex;gap:10px}
.hero-title{position:absolute;left:207px;top:290px;width:815px;height:95px;border-top:2px solid rgba(255,255,255,.8);border-bottom:2px solid rgba(255,255,255,.8);display:flex;align-items:center;justify-content:center;gap:24px;color:var(--white);font-size:32px;font-weight:700;white-space:nowrap;letter-spacing:.3px}
.hero-title .divider{width:2px;height:56px;background:rgba(255,255,255,.8);flex:none}

/* welcome */
.welcome{top:672px;height:546px}
.welcome-art{position:absolute;left:150px;top:40px;width:445px;height:460px;background:linear-gradient(135deg,#f2f2f2,#e6e6e6);border-radius:6px}
.welcome-text{position:absolute;left:648px;top:48px;width:413px}
.welcome-text .eyebrow{font-size:22px}
.welcome-text h1{font-size:32px;color:var(--ink);margin-top:6px;white-space:nowrap}
.rule{width:56px;height:2px;background:var(--blue);margin:22px 0 34px}
.welcome-text p{font-size:13.5px;line-height:22.5px;text-align:justify;margin-bottom:22px}
.welcome-text .btn{margin-top:8px;padding:13px 20px}

/* proficiency */
.proficiency{top:1218px;height:232px;text-align:center;color:var(--white)}
.proficiency h2{font-size:32px;margin-top:46px}
.proficiency .lead{font-size:18px;margin-top:12px}
.challenge-note{display:inline-block;margin-top:30px;border:1.5px solid rgba(255,255,255,.85);padding:10px 20px;font-size:14px;white-space:nowrap}

/* challenges */
.challenges{top:1450px;height:520px;background:var(--paper)}
.card{position:absolute;background:linear-gradient(180deg,var(--blue-soft),#f6f8fd);border-radius:4px;text-align:center;padding:24px 22px}
.card svg{display:block;margin:0 auto 12px}
.card h3{font-family:'Montserrat',sans-serif;font-weight:600;font-size:16px;color:var(--ink);line-height:21px}
.card p{font-size:11.5px;line-height:18px;margin-top:8px;color:var(--muted)}

/* how */
.how{top:1970px;height:205px;text-align:center;color:var(--white)}
.how h2{font-size:32px;margin-top:45px;white-space:nowrap}
.how p{font-size:18px;line-height:28px;margin-top:12px}

/* methodology */
.method{top:2175px;height:494px}
.col-label{position:absolute;top:48px;font-family:'Montserrat',sans-serif;font-weight:700;font-size:14px;color:var(--ink)}
.feature{position:absolute;width:437px;background:linear-gradient(90deg,#ffffff,#eef3fc);border:1.5px solid var(--line);border-radius:6px;padding:18px 30px}
.feature-head{display:flex;align-items:center;gap:15px}
.feature-icon{width:50px;height:50px;border-radius:50%;background:var(--blue);display:flex;align-items:center;justify-content:center;flex:none}
.feature h3{font-family:'Montserrat',sans-serif;font-weight:600;font-size:15.5px;color:var(--ink)}
.feature p{font-size:11.5px;line-height:16px;margin-top:18px;color:var(--body)}

/* lesson */
.lesson{top:2669px;height:535px;text-align:center;color:var(--white)}
.lesson h2{font-size:32px;margin-top:64px}
.lesson .short-rule{width:56px;height:2px;background:var(--white);margin:22px auto 0}
.lesson h3{font-family:'Montserrat',sans-serif;font-weight:600;font-size:24px;margin-top:44px}
.tabs{display:flex;justify-content:center;gap:15px;margin-top:28px}
.tab{font-family:'Montserrat',sans-serif;font-weight:600;font-size:15px;padding:10px 22px;border:1.5px solid rgba(255,255,255,.8);color:var(--white)}
.tab.active{background:var(--blue);border-color:var(--blue)}
.step{position:absolute;top:304px;width:235px;height:175px;background:var(--white);color:var(--body);padding:24px 18px}
.step .time{display:inline-block;border:1px solid var(--blue);color:var(--blue);font-size:13px;padding:3px 8px}
.step h4{font-family:'Montserrat',sans-serif;font-weight:600;font-size:15px;color:var(--ink);margin-top:14px}
.step p{font-size:11px;line-height:15px;margin-top:10px}
.arrow{position:absolute;top:384px}

/* footer */
.footer{top:3204px;height:311px;background:var(--footer);color:var(--white)}
.footer .brand{left:162px;top:40px}
.footer-cta{position:absolute;left:158px;top:140px;display:flex;gap:10px}
.footer-col{position:absolute;top:38px}
.footer-col h5{font-family:'Montserrat',sans-serif;font-weight:600;font-size:14px;margin-bottom:18px}
.footer-col a{display:block;color:#b9bfcc;font-size:12.5px;text-decoration:none;margin-bottom:9px}
.contact-row{display:flex;gap:14px;font-size:12.5px;color:#b9bfcc;line-height:18px;margin-bottom:18px}
.socials{display:flex;gap:7px}
.social{width:32px;height:32px;border-radius:50%;background:var(--white)}
.copyright{position:absolute;left:0;right:0;top:262px;text-align:center;font-size:12.5px;color:#b9bfcc}
</style>
</head>
<body>

<header class="section hero chalkboard">
  <div class="hero-bg" role="img" aria-label="Green chalkboard covered with handwritten math formulas"></div>
  <div class="brand">
    <span class="brand-mark"></span>
    <div>
      <div class="brand-name">Brevanta Numérica</div>
      <div class="brand-tag">Inspiring Math . Empowering Learning</div>
    </div>
  </div>
  <nav class="nav">
    <a href="#" class="active">FEATURES</a>
    <a href="#">PROGRAM</a>
    <a href="#">TUITION</a>
    <a href="#">ABOUT US</a>
    <a href="#">CONTACT US</a>
  </nav>
  <div class="nav-cta">
    <a href="#" class="btn btn-blue">Register a Student</a>
    <a href="#" class="btn btn-white">Free Consultation</a>
  </div>
  <div class="hero-title heading">
    <span>Inspiring Math</span><span class="divider"></span><span>Empowering Learning</span>
  </div>
</header>

<section class="section welcome">
  <div class="welcome-art" role="img" aria-label="Line illustration of a teacher at a whiteboard connected to three students at laptops"></div>
  <div class="welcome-text">
    <div class="heading eyebrow" style="color:var(--ink)">Welcome to</div>
    <h1 class="heading">Brevanta Numérica</h1>
    <div class="rule"></div>
    <p>Brevanta Numérica – accelerated educational outcome is a comprehensive online math curriculum teaching service for independently schooled students in grades 6 through 12 worldwide. Teaching is done through our math academy, a one-on-one, virtual adaptive classroom that uses integrated, interactive digital whiteboards for both teachers and students. Brevanta Math Academy will open its virtual doors for the first cohort of grade 6 students in September 2026.</p>
    <p>Registration for Term One math classes opens on June 1, 2026 and closes in the middle of August 2026.</p>
    <a href="#" class="btn btn-blue">Read More</a>
  </div>
</section>

<section class="section proficiency chalkboard">
  <h2 class="heading">Proficiency</h2>
  <p class="lead">Making math education engaging, effective, and within everyone’s reach.</p>
  <div class="challenge-note">Teaching math to independently schooled students is not easy. We know the challenges:</div>
</section>

<section class="section challenges">
  <div class="card" style="left:147px;top:43px;width:288px;height:163px">
    <svg width="46" height="50" viewBox="0 0 46 50" fill="none" stroke="#3b82f6" stroke-width="2"><rect x="6" y="6" width="30" height="40" rx="2"/><path d="M13 18h16M13 26h16M13 34h10"/></svg>
    <h3>Limited subject expertise</h3>
    <p>Struggling with advanced topics, forgotten knowledge, and specialized methods.</p>
  </div>
  <div class="card" style="left:446px;top:43px;width:288px;height:163px">
    <svg width="46" height="50" viewBox="0 0 46 50" fill="none" stroke="#3b82f6" stroke-width="2"><circle cx="20" cy="28" r="11"/><circle cx="33" cy="14" r="7"/></svg>
    <h3>Ensuring conceptual understanding</h3>
    <p>Over-reliance on procedures. Bridging the “why” of math and real-world applications.</p>
  </div>
  <div class="card" style="left:747px;top:43px;width:288px;height:163px">
    <svg width="46" height="50" viewBox="0 0 46 50" fill="none" stroke="#3b82f6" stroke-width="2"><rect x="8" y="4" width="30" height="42" rx="2"/><path d="M14 14h18M14 22h18M15 34l8-4 8 4-8 4z"/></svg>
    <h3>Curriculum challenges</h3>
    <p>How can I choose the right curriculum and supplementary materials? Can I successfully adapt pre-made plans?</p>
  </div>
  <div class="card" style="left:147px;top:266px;width:288px;height:202px">
    <svg width="46" height="50" viewBox="0 0 46 50" fill="none" stroke="#3b82f6" stroke-width="2"><rect x="4" y="8" width="38" height="26" rx="1"/><path d="M23 34v6M16 46l7-6 7 6M10 16h10M10 24h10M26 16h10M26 24h10"/></svg>
    <h3>Preparing for advanced math</h3>
    <p>Am I preparing my child for advanced math and for successfully transitioning into higher education, skilled jobs, or entrepreneurship?</p>
  </div>
  <div class="card" style="left:446px;top:266px;width:288px;height:202px">
    <svg width="46" height="50" viewBox="0 0 46 50" fill="none" stroke="#3b82f6" stroke-width="2"><rect x="6" y="4" width="26" height="40" rx="2"/><circle cx="31" cy="32" r="8"/><path d="M37 38l6 6M12 12h14M12 20h10"/></svg>
    <h3>Assessment and feedback</h3>
    <p>Am I using the proper evaluation process to assess my child’s progress and identify their weaknesses? Am I providing timely feedback to my child?</p>
  </div>
  <div class="card" style="left:747px;top:266px;width:288px;height:202px">
    <svg width="46" height="50" viewBox="0 0 46 50" fill="none" stroke="#3b82f6" stroke-width="2"><rect x="6" y="10" width="28" height="34" rx="2" transform="rotate(-12 20 27)"/><path d="M32 6l8 8-14 14h-6v-6z"/></svg>
    <h3>Keeping math fun<br>and engaging</h3>
    <p>Creativity struggles, gamification challenges and overcoming math fatigue.</p>
  </div>
</section>

<section class="section how chalkboard">
  <h2 class="heading">How Brevanta Numérica Works</h2>
  <p>Teaching comprehensive math curricula to independently schooled<br>students in grades 6-12 through secure virtual classrooms.</p>
</section>

<section class="section method">
  <div class="col-label" style="left:149px">PEDAGOGICAL METHODOLOGY</div>
  <div class="col-label" style="left:613px">VIRTUAL CLASSROOM</div>

  <div class="feature" style="left:147px;top:84px;height:191px">
    <div class="feature-head">
      <span class="feature-icon"><svg width="24" height="24" viewBox="0 0 24 24" fill="none" stroke="#fff" stroke-width="1.8"><rect x="5" y="3" width="14" height="18" rx="1"/><path d="M9 9h6M9 13h6M9 17h4"/></svg></span>
      <h3>Effective Curriculum</h3>
    </div>
    <p>Time-tested and proven pedagogical methodology with three pillars: (1) new math concepts built on previously taught ones; (2) daily review of earlier math concepts to increase understanding; and (3) frequent, cumulative assessments to ensure students master each math skill as new ones are added.</p>
  </div>
  <div class="feature" style="left:611px;top:84px;height:191px">
    <div class="feature-head">
      <span class="feature-icon"><svg width="24" height="24" viewBox="0 0 24 24" fill="none" stroke="#fff" stroke-width="1.8"><rect x="3" y="4" width="18" height="12" rx="1"/><path d="M12 16v3M8 22l4-3 4 3"/></svg></span>
      <h3>Personalized Whiteboards</h3>
    </div>
    <p>Every student gets an individual digital whiteboard, where they can draw, write text and equations, work on practice problems, homework, and tests. The students only see the teacher and their whiteboard.</p>
  </div>
  <div class="feature" style="left:147px;top:290px;height:148px">
    <div class="feature-head">
      <span class="feature-icon"><svg width="24" height="24" viewBox="0 0 24 24" fill="none" stroke="#fff" stroke-width="1.8"><circle cx="12" cy="11" r="6"/><path d="M9 19h6M10 22h4"/></svg></span>
      <h3>Innovative Lesson Design</h3>
    </div>
    <p>Standard, modular 1 ½ hour lesson workflows designed to accelerate students’ mastery of math skills and concepts.</p>
  </div>
  <div class="feature" style="left:611px;top:290px;height:148px">
    <div class="feature-head">
      <span class="feature-icon"><svg width="24" height="24" viewBox="0 0 24 24" fill="none" stroke="#fff" stroke-width="1.8"><circle cx="12" cy="12" r="3"/><path d="M12 3v4M12 17v4M3 12h4M17 12h4"/></svg></span>
      <h3>Interactive Sessions</h3>
    </div>
    <p>Engage with dynamic content, real-time problem solving and feedback, and interactive tools that make math concepts come alive.</p>
  </div>
</section>

<section class="section lesson chalkboard">
  <h2 class="heading">Innovative Lesson</h2>
  <div class="short-rule"></div>
  <h3>1 and ½ Hour Session Lesson Workflow</h3>
  <div class="tabs">
    <span class="tab">Grades 6 to 8</span>
    <span class="tab active">Grades 9 to 12</span>
  </div>

  <div class="step" style="left:149px">
    <span class="time">25 minutes</span>
    <h4>NEW CONCEPTS</h4>
    <p>Introduces new math concepts in small increments.</p>
  </div>
  <svg class="arrow" style="left:390px" width="84" height="14" viewBox="0 0 84 14"><path d="M0 7h72" stroke="#fff" stroke-width="2"/><path d="M72 1l12 6-12 6z" fill="#fff"/></svg>
  <div class="step" style="left:482px">
    <span class="time">20 minutes</span>
    <h4>LESSON PRACTICE</h4>
    <p>Opportunity for students to practice skills of new math concepts.</p>
  </div>
  <svg class="arrow" style="left:720px" width="84" height="14" viewBox="0 0 84 14"><path d="M0 7h72" stroke="#fff" stroke-width="2"/><path d="M72 1l12 6-12 6z" fill="#fff"/></svg>
  <div class="step" style="left:811px">
    <span class="time">45 minutes</span>
    <h4>HOMEWORK</h4>
    <p>Twenty-five to thirty problems to provide students with distributed practice that promote long-term retention of math concepts.</p>
  </div>
</section>

<footer class="section footer">
  <div class="brand">
    <span class="brand-mark"></span>
    <div>
      <div class="brand-name">Brevanta Numérica</div>
      <div class="brand-tag">Inspiring Math . Empowering Learning</div>
    </div>
  </div>
  <div class="footer-cta">
    <a href="#" class="btn btn-blue">Register a Student</a>
    <a href="#" class="btn btn-white">Free Consultation</a>
  </div>
  <div class="footer-col" style="left:526px">
    <h5>Menu</h5>
    <a href="#">Features</a><a href="#">Program</a><a href="#">Tuition</a><a href="#">About Us</a><a href="#">Contact Us</a>
  </div>
  <div class="footer-col" style="left:642px">
    <h5>Contact Us</h5>
    <div class="contact-row">
      <svg width="12" height="16" viewBox="0 0 12 16"><path d="M6 0a6 6 0 0 0-6 6c0 4.5 6 10 6 10s6-5.5 6-10a6 6 0 0 0-6-6zm0 8.5A2.5 2.5 0 1 1 6 3.5a2.5 2.5 0 0 1 0 5z" fill="#fff"/></svg>
      <span>Larkfield, Alberta,<br>Canada</span>
    </div>
    <div class="contact-row">
      <svg width="13" height="13" viewBox="0 0 24 24"><path d="M6.6 10.8a15.1 15.1 0 0 0 6.6 6.6l2.2-2.2a1 1 0 0 1 1-.25 11.4 11.4 0 0 0 3.6.57 1 1 0 0 1 1 1V20a1 1 0 0 1-1 1A17 17 0 0 1 3 4a1 1 0 0 1 1-1h3.5a1 1 0 0 1 1 1c0 1.25.2 2.45.57 3.6a1 1 0 0 1-.25 1z" fill="#fff"/></svg>
      <span>+1 555 014 2290</span>
    </div>
  </div>
  <div class="footer-col" style="left:855px">
    <h5>Follow Us</h5>
    <div class="socials">
      <span class="social"></span><span class="social"></span><span class="social"></span><span class="social"></span><span class="social"></span>
    </div>
  </div>
  <div class="copyright">Copyright © 2026 All Rights Reserved</div>
</footer>

</body>
</html>
```